kolvarin.link kolvarin.space kolvarin.press website

The website is named KOLVARIN and it will have 3 domain names. kolvarin.link, press, space.
I'd like it to be viewed on Pads, pcs and phones.

page menu:

kolvarin.link(start page): presentation of company. (creative, design, app, new product innovation.)
Here we'll need sosial media icons: plimber, vendoloop, mirtavel, trelvanet. (light but some 'fruity' colors)

kolvarin.press: blog. It will be a 75% picture blog > rest will be text. I need to be able to resize pictures and shape columns to picture size. (light but some 'fruity' colors)

kolvarin.space : the fun part of this web design, however, on entering the page I'd like a non-disclosure agreement where viewer simply click "yes, I agree" after filling out contact info. (check attached document)
We will have space here for uploading PDF files viewers can download. There is also a blog space here to tell in brief about the PDF file. (maybe a space/sci-fi theme her e.g spacechimp, Laika the space dog?)

I will attach the logo here I want you to use > and develop for the .space .press webpage. The logo i uploaded is for the .link page.

Target Market(s)

venture capitalists

Number of Pages Required

3 page

Requirements
Must have
• a few 'fruity colors' but mostly white and grey

```html
<!DOCTYPE html>
<html lang="en">
<head>
<meta charset="utf-8">
<title>Kolvarin Link</title>
<link href="https://fonts.googleapis.com/css2?family=Jost:wght@400;500;600&family=Lato:ital,wght@0,400;0,700;1,400&display=swap" rel="stylesheet">
<style>
:root{
  --ink:#111111;
  --text:#333333;
  --muted:#777777;
  --line:#cfcfcf;
  --panel:#f2f2f2;
  --green:#5a9a3e;
  --red:#e04b31;
  --orange:#f6ab1a;
  --accent:#e08a22;
  --cream:#fbf7c9;
  --white:#ffffff;
  --footer:#111111;
  --paper:#ebe8e1;
}
*{box-sizing:border-box;margin:0;padding:0}
html,body{width:1200px;height:2261px;overflow:hidden;background:var(--white)}
body{position:relative;font-family:"Lato",sans-serif;color:var(--text)}
h1,h2,h3{font-family:"Jost",sans-serif;font-weight:500;color:var(--ink)}
h2 span{color:var(--accent)}

/* header */
.site-header{position:absolute;left:0;top:0;width:1200px;height:151px;background:var(--white);box-shadow:0 2px 4px rgba(0,0,0,.12);z-index:2}
.brand{position:absolute;left:98px;top:18px;display:flex;align-items:center;gap:12px}
.brand-mark{width:34px;height:34px;background:var(--orange)}
.brand-name{font-family:"Jost",sans-serif;font-weight:600;font-size:40px;color:var(--ink);letter-spacing:1px}
.social{position:absolute;display:flex}
.social .dot{border-radius:50%;display:flex;align-items:center;justify-content:center;font-family:"Lato",sans-serif;font-weight:700}
.header-social{left:861px;top:15px;gap:14px}
.header-social .dot{width:30px;height:30px;background:#e8e8e8;color:var(--ink);font-size:14px}
.menu-btn{position:absolute;left:1062px;top:14px;width:38px;height:34px;border:2px solid var(--red);border-radius:3px;padding:7px 6px;display:flex;flex-direction:column;justify-content:space-between}
.menu-btn i{display:block;height:3px;background:var(--red)}
.contact{position:absolute;top:83px;display:flex;align-items:center;gap:8px;font-size:15px;line-height:17px;color:var(--ink)}
.contact .ico{width:36px;height:36px;border-radius:50%;border:2px solid #bbb;display:flex;align-items:center;justify-content:center}
.contact b{font-weight:700;font-size:14px}

/* hero */
.hero{position:absolute;left:0;top:151px;width:1200px;height:550px;background:linear-gradient(135deg,#eeebe4,#e6e2d9 60%,#ece9e2);overflow:hidden}
.hero-flourish{position:absolute;left:700px;top:0;width:500px;height:200px;background:radial-gradient(ellipse at 45% 0%,rgba(214,120,200,.35),rgba(120,210,200,.18) 45%,rgba(235,232,225,0) 72%)}
.hero-flourish.low{left:-120px;top:330px;width:300px;height:260px;background:radial-gradient(ellipse at 30% 80%,rgba(150,210,120,.35),rgba(214,120,200,.15) 45%,rgba(235,232,225,0) 72%)}
.hero-device{position:absolute;left:430px;top:75px;width:743px;height:370px;background:
  radial-gradient(ellipse at 60% 40%,rgba(255,255,255,.85),rgba(255,255,255,0) 60%),
  linear-gradient(180deg,rgba(222,222,222,.9),rgba(200,200,200,.7) 75%,rgba(235,232,225,0));border-radius:24px;filter:blur(2px)}
.hero-title{position:absolute;left:98px;top:168px;font-family:"Jost",sans-serif;font-weight:600;font-size:30px;line-height:50px;letter-spacing:1px;color:#2a2a2a}
.btn-contact{position:absolute;left:98px;top:288px;width:128px;height:47px;background:var(--green);color:var(--white);font-family:"Jost",sans-serif;font-weight:500;font-size:20px;display:flex;align-items:center;justify-content:center;border-radius:2px}
.slider-dots{position:absolute;display:flex;gap:9px}
.slider-dots i{width:11px;height:11px;border-radius:50%;background:#cccccc}
.hero .slider-dots{left:98px;top:356px}
.hero .slider-dots i:first-child{background:var(--orange)}

/* about */
.about{position:absolute;left:0;top:701px;width:1200px;height:388px;background:var(--panel)}
.about h2{position:absolute;left:100px;top:44px;font-size:39px}
.about .rule{position:absolute;left:100px;top:110px;width:627px;height:1px;background:var(--line)}
.about-lead{position:absolute;left:100px;top:126px;font-weight:700;font-size:16.5px;color:var(--ink)}
.about-body{position:absolute;left:100px;top:155px;width:622px;font-size:16.5px;line-height:31px;color:var(--text)}
.about .divider{position:absolute;left:772px;top:55px;width:1px;height:280px;background:var(--line)}
.inquiry h2{position:absolute;left:825px;top:44px;font-size:39px}
.field{position:absolute;left:826px;width:275px;height:32px;background:var(--white);border:1px solid #d4d4d4;font-size:13px;color:var(--muted);padding:8px 8px}
.btn-submit{position:absolute;left:826px;top:314px;width:112px;height:33px;background:var(--red);color:var(--white);font-family:"Jost",sans-serif;font-weight:600;font-size:16px;letter-spacing:1px;display:flex;align-items:center;justify-content:center;gap:8px;border-radius:2px}
.btn-submit i{width:20px;height:20px;border-radius:50%;background:#3a3a3a;display:flex;align-items:center;justify-content:center}

/* section headings */
.section-head{position:absolute;left:0;width:1200px;text-align:center}
.section-head h2{font-size:39px}
.head-rule{position:absolute;height:1px;background:var(--line)}
.head-badge{position:absolute;width:22px;height:26px;border-radius:50%;background:var(--orange)}

/* offer */
.offers{position:absolute;left:100px;top:1270px;width:1001px;height:353px;display:flex;border-radius:3px;overflow:hidden}
.offer{flex:1;text-align:center;color:var(--white);padding-top:54px}
.offer.design{background:var(--green)}
.offer.app{background:var(--red)}
.offer.innovation{background:var(--orange)}
.offer svg{display:block;margin:0 auto;height:108px}
.offer h3{font-weight:600;color:var(--white);font-size:19px;letter-spacing:1px;margin-top:50px}
.offer p{font-size:14px;line-height:22px;margin:18px auto 0;width:275px}

/* testimonials */
.testimonials{position:absolute;left:0;top:1691px;width:1200px;height:520px;background:var(--cream)}
.quote-card{position:absolute;top:173px;width:465px;height:134px;background:var(--white);border:1px solid #dddddd;border-radius:6px;padding:14px 16px 0 48px;font-style:italic;font-size:12.5px;line-height:20px;color:var(--ink)}
.quote-card .mark{position:absolute;left:14px;top:8px;font-family:"Jost",sans-serif;font-style:normal;font-size:40px;color:#cccccc;line-height:40px}
.quote-card svg.tail{position:absolute;left:350px;bottom:-26px}
.avatar{position:absolute;width:106px;height:106px;border-radius:50%;border:2px solid var(--orange);background:linear-gradient(160deg,#c9a489,#8a5a43)}
.avatar-badge{position:absolute;width:46px;height:46px;border-radius:50%;background:var(--red);color:var(--white);font-family:"Jost",sans-serif;font-size:32px;display:flex;align-items:center;justify-content:center;line-height:1}
.author{position:absolute;font-size:15px;color:var(--ink)}
.author span{color:var(--muted);border-left:2px solid var(--orange);padding-left:9px;margin-left:9px}
.testimonials .slider-dots{left:566px;top:454px}
.testimonials .slider-dots i:first-child{background:var(--green)}

/* footer */
.site-footer{position:absolute;left:0;top:2211px;width:1200px;height:50px;background:var(--footer)}
.site-footer p{position:absolute;left:98px;top:17px;font-size:13px;color:#dddddd}
.footer-social{left:931px;top:9px;gap:15px}
.footer-social .dot{width:32px;height:32px;background:var(--white);color:var(--footer);font-size:15px}
</style>
</head>
<body>

<header class="site-header">
  <div class="brand"><div class="brand-mark"></div><div class="brand-name">KOLVARIN</div></div>
  <nav class="social header-social" aria-label="Social links">
    <span class="dot">p</span><span class="dot">v</span><span class="dot">m</span><span class="dot">t</span>
  </nav>
  <div class="menu-btn" aria-label="Menu"><i></i><i></i><i></i></div>
  <div class="contact" style="left:720px">
    <span class="ico"><svg width="18" height="18" viewBox="0 0 24 24"><path fill="#5a9a3e" d="M6.6 10.8a15 15 0 0 0 6.6 6.6l2.2-2.2a1 1 0 0 1 1-.25 11.4 11.4 0 0 0 3.6.57 1 1 0 0 1 1 1V20a1 1 0 0 1-1 1A17 17 0 0 1 3 4a1 1 0 0 1 1-1h3.5a1 1 0 0 1 1 1c0 1.25.2 2.45.57 3.57a1 1 0 0 1-.25 1z"/></svg></span>
    <div><b>Call Us</b><br>(555)-210-4487</div>
  </div>
  <div class="contact" style="left:907px">
    <span class="ico"><svg width="18" height="14" viewBox="0 0 18 14"><rect width="18" height="14" rx="1" fill="#5a9a3e"/><path d="M1 1l8 6 8-6" stroke="#fff" stroke-width="1.6" fill="none"/></svg></span>
    <div><b>Email Us</b><br>info@kolvarinlink.com</div>
  </div>
</header>

<section class="hero">
  <div class="hero-flourish" role="img" aria-label="Colourful floral swirl decoration"></div>
  <div class="hero-flourish low" role="img" aria-label="Colourful floral swirl decoration"></div>
  <div class="hero-device" role="img" aria-label="Laptop showing a sample website layout"></div>
  <h1 class="hero-title">WE DESIGN &amp; DEVELOP<br>YOUR DREAMS</h1>
  <div class="btn-contact">Contact Us</div>
  <div class="slider-dots"><i></i><i></i><i></i><i></i></div>
</section>

<section class="about">
  <h2>About <span>Kolvarin Link</span></h2>
  <div class="rule"></div>
  <p class="about-lead">Lorem ipsum dolor sit amet, consectetuer in the adipiscing elit...</p>
  <p class="about-body">Lorem ipsum dolor sit amet, consectetuer adipiscing elit, sed diam nonummy nibh euismod tincidunt ut laoreet dolore magna aliquam erat volutpat. Ut wisi enim ad minim veniam, quis nostrud exercisei tation ullamcorper suscipit lobortis nisl ut aliquip ex ea commodo consequat. Duis autem vel eumorl iriure dolor in hendrerit in vulputate velit esse molestie consequat, vel illum dolore eu feugiat nullam facilisis at vero eros et accumsan et iusto odio&nbsp; facilisi.....</p>
  <div class="divider"></div>
  <div class="inquiry">
    <h2>Quick <span>Inquiry</span></h2>
    <div class="field" style="top:109px">Name</div>
    <div class="field" style="top:150px">Email</div>
    <div class="field" style="top:192px">Phone</div>
    <div class="field" style="top:234px;height:65px">Messages</div>
    <div class="btn-submit">SUBMIT <i><svg width="8" height="10" viewBox="0 0 8 10"><path d="M2 1l4 4-4 4" stroke="#fff" stroke-width="2" fill="none"/></svg></i></div>
  </div>
</section>

<div class="section-head" style="top:1130px"><h2>What We <span>Offer</span></h2></div>
<div class="head-rule" style="left:380px;top:1209px;width:440px"></div>
<div class="head-badge" style="left:589px;top:1195px"></div>

<section class="offers">
  <div class="offer design">
    <svg viewBox="0 0 112 108" width="112"><rect x="4" y="4" width="104" height="100" rx="8" fill="#fff"/><rect x="16" y="26" width="80" height="66" fill="#5a9a3e"/><circle cx="20" cy="15" r="3.5" fill="#5a9a3e"/><circle cx="31" cy="15" r="3.5" fill="#5a9a3e"/><circle cx="42" cy="15" r="3.5" fill="#5a9a3e"/><path d="M44 44l32 32" stroke="#fff" stroke-width="7" stroke-linecap="round"/><path d="M72 72l12 12-4 4-12-12z" fill="#fff"/></svg>
    <h3>CREATIVE DESIGN</h3>
    <p>Lorem ipsum dolor sit amet, sed diam nonummy nibh euismod tincidunt ut laoreet dolore. Lorem ipsum dolor sit amet</p>
  </div>
  <div class="offer app">
    <svg viewBox="0 0 100 108" width="100"><rect x="6" y="2" width="54" height="104" rx="8" fill="#fff"/><rect x="13" y="16" width="40" height="72" fill="#e04b31"/><rect x="19" y="26" width="14" height="5" fill="#fff"/><rect x="19" y="40" width="10" height="5" fill="#fff"/><rect x="19" y="54" width="14" height="5" fill="#fff"/><circle cx="33" cy="97" r="4" fill="#e04b31"/><circle cx="68" cy="56" r="22" fill="#fff"/><g fill="#fff"><rect x="64" y="28" width="8" height="10"/><rect x="64" y="74" width="8" height="10"/><rect x="40" y="52" width="10" height="8"/><rect x="86" y="52" width="10" height="8"/></g><circle cx="68" cy="56" r="8" fill="#e04b31"/></svg>
    <h3>APP DEVELOPMENT</h3>
    <p>Lorem ipsum dolor sit amet, sed diam nonummy nibh euismod tincidunt ut laoreet dolore. Lorem ipsum dolor sit amet</p>
  </div>
  <div class="offer innovation">
    <svg viewBox="0 0 96 108" width="96"><path d="M48 6c-24 0-40 17-40 38 0 10 4 16 8 22v38h44V90h14c6 0 8-4 8-8V70l8-4-8-14C80 26 70 6 48 6z" fill="#fff"/><circle cx="44" cy="42" r="15" fill="#f6ab1a"/><rect x="38" y="58" width="12" height="10" fill="#f6ab1a"/><g stroke="#f6ab1a" stroke-width="3"><path d="M44 18v-6"/><path d="M26 26l-4-4"/><path d="M62 26l4-4"/></g></svg>
    <h3>NEW PRODUCT INNOVATION</h3>
    <p>Lorem ipsum dolor sit amet, sed diam nonummy nibh euismod tincidunt ut laoreet dolore. Lorem ipsum dolor sit amet</p>
  </div>
</section>

<section class="testimonials">
  <div class="section-head" style="top:48px"><h2>Client <span>Testimonials</span></h2></div>
  <div class="head-rule" style="left:347px;top:126px;width:437px"></div>
  <div class="head-badge" style="left:555px;top:112px"></div>

  <div class="quote-card" style="left:110px"><span class="mark">&ldquo;</span>Lorem ipsum dolor sit amet, sed diam nonummy nibh euismod tincidunt ut laoreet dolore. Lorem ipsum dolor sit amet, sed diam nonummy nibh euismod tincidunt ut laoreet dolore. Lorem ipsum dolor sit amet, sed diam nonummy nibh euismod tincidunt ut laoreet dolore.
    <svg class="tail" width="44" height="28" viewBox="0 0 44 28"><path d="M0 0h44L4 27z" fill="#fff" stroke="#ddd"/><path d="M1 0h42" stroke="#fff" stroke-width="3"/></svg></div>
  <div class="avatar" style="left:98px;top:271px" role="img" aria-label="Client portrait"></div>
  <div class="avatar-badge" style="left:170px;top:338px">&ldquo;</div>
  <div class="author" style="left:314px;top:349px">Marla Voskin<span>Customer</span></div>

  <div class="quote-card" style="left:635px"><span class="mark">&ldquo;</span>Lorem ipsum dolor sit amet, sed diam nonummy nibh euismod tincidunt ut laoreet dolore. Lorem ipsum dolor sit amet, sed diam nonummy nibh euismod tincidunt ut laoreet dolore. Lorem ipsum dolor sit amet, sed diam nonummy nibh euismod tincidunt ut laoreet dolore.
    <svg class="tail" width="44" height="28" viewBox="0 0 44 28"><path d="M0 0h44L4 27z" fill="#fff" stroke="#ddd"/><path d="M1 0h42" stroke="#fff" stroke-width="3"/></svg></div>
  <div class="avatar" style="left:623px;top:271px" role="img" aria-label="Client portrait"></div>
  <div class="avatar-badge" style="left:695px;top:338px">&ldquo;</div>
  <div class="author" style="left:838px;top:349px">Marla Voskin<span>Customer</span></div>

  <div class="slider-dots"><i></i><i></i><i></i><i></i></div>
</section>

<footer class="site-footer">
  <p>Copyright &copy; 2016 Kolvarin Link. All Rights Reserved.</p>
  <nav class="social footer-social" aria-label="Social links">
    <span class="dot">p</span><span class="dot">v</span><span class="dot">m</span><span class="dot">t</span>
  </nav>
</footer>

</body>
</html>
```